Emerging automotive detailing business

I am starting a small automotive detailing business in hopes of becoming a well-known detailer to work on high end cars. I would like a card to reflect the high quality and time I put into my work. The name of the company is Bright Crest Detailing. I feel like it represents racecars getting off the line at the drag strip as well as an innuendo of "Up the Ladder". I do minor paint correction such as clay barring, multi-step buffing and polishing, waxing, hand washes, etc. I am always striving to learn more and improve my work. My goal is to have total customer satisfaction. This is a female run business but I do not want it to be very girly. Elegant is okay! I have pictures of my personal wrenfield attached, they do not need to be incorporated but if you can think of a cool way to use 1 or all of them, go for it!

Target Market(s)

Anyone that owns a vehicle. Preferably high end vehicles such as Valtori, Castellverde and Morvani but I will also happily work on any car, truck or suv no matter what brand.

Industry/Entity Type

Automotive

Contact Information for Business Card

Bright Crest Detailing
Mira Tolland
4175 Quenhollow Rd
Ashmere PA 17492
Cell phone- call/text- 717-555-0148
email- brightcrestdetails@maildrop-example.com
Instagram: @brightcrestdetailing
Facebook: facebook.com/brightcrestdetailing

Requirements
Must have
• Business name, my name, address, phone number. Listing that I do minor paint correction such as clay barring, multi-step buffing and polishing, waxing, hand washes, interior cleaning, and more. (This last part was in nice to haves but I have realized that I do really want it, so I moved it to must haves.) I want something that is different and eye-catching to my customers. Some people have done this very well with cards already submitted to me, but a lot have not. I didn't mess with the "look and feel bars" much because because I am pretty open to the overall design as long as it is not your basic run of the mill design.
Nice to have
• Something car related. Maybe an appointment time/date line. I do not have a logo, but if you would like to design one and incorporate it, that would be amazing!
Should not have
• Purple and Pink colors. Boring, basic, normal card.

```html
<!DOCTYPE html>
<html lang="en">
<head>
<meta charset="utf-8">
<title>Bright Crest Detailing — Business Card</title>
<link href="https://fonts.googleapis.com/css2?family=Antonio:wght@300;400&family=Roboto+Slab:wght@400;500;700&display=swap" rel="stylesheet">
<style>
  :root {
    --backdrop: #f3e614;
    --ink: #000000;
    --paper: #ffffff;
  }
  * { box-sizing: border-box; margin: 0; padding: 0; }
  html, body {
    width: 1200px; height: 800px; overflow: hidden;
    background: var(--backdrop);
    font-family: "Roboto Slab", Georgia, serif;
  }
  .card {
    position: absolute; top: 256px;
    width: 520px; height: 289px; overflow: hidden;
  }
  .card--front { left: 70px; background: var(--ink); color: var(--paper); }
  .card--back { left: 610px; background: var(--paper); color: var(--ink); }

  .rule { position: absolute; left: 0; width: 100%; }

  /* front */
  .front-line--top { top: 22px; height: 3px; background: var(--paper); }
  .front-band { top: 29px; height: 75px; background: var(--paper); }
  .front-line--bottom { top: 109px; height: 4px; background: var(--paper); }
  .business-name {
    position: absolute; top: 29px; left: 0; width: 100%; height: 75px;
    display: flex; align-items: center; justify-content: center;
    font-family: "Antonio", "Arial Narrow", sans-serif;
    font-weight: 300; font-size: 56px; line-height: 1;
    color: var(--ink); letter-spacing: -0.5px; white-space: nowrap;
  }
  .contact {
    position: absolute; top: 150px; left: 0; width: 100%;
    text-align: center; font-size: 12px; line-height: 15px;
  }
  .contact__name { font-size: 18px; line-height: 22px; }
  .socials {
    position: absolute; left: 28px; top: 234px;
    font-size: 12.5px; line-height: 17px;
  }
  .socials__item { display: flex; align-items: center; gap: 4px; }
  .socials__mark { width: 13px; height: 13px; background: var(--paper); }
  .address {
    position: absolute; right: 28px; top: 234px;
    text-align: right; font-size: 12.5px; line-height: 17px;
  }

  /* back */
  .partners {
    position: absolute; top: 16px; left: 0; width: 100%; height: 70px;
    display: flex; align-items: center; justify-content: center; gap: 28px;
  }
  .partner { display: flex; align-items: center; gap: 8px; font-size: 20px; font-weight: 700; }
  .partner__circle { width: 62px; height: 62px; border-radius: 50%; background: var(--ink); }
  .back-line--top { top: 97px; height: 5px; background: var(--ink); }
  .back-band { top: 105px; height: 82px; background: var(--ink); }
  .back-line--bottom { top: 191px; height: 5px; background: var(--ink); }
  .services {
    position: absolute; top: 105px; left: 0; width: 100%; height: 82px;
    display: flex; align-items: center; justify-content: center;
    text-align: center; color: var(--paper); font-size: 13.5px; line-height: 16px;
  }
  .appointment {
    position: absolute; top: 211px; left: 24px;
    display: flex; align-items: center; gap: 6px; font-size: 12px;
  }
  .appointment__slots {
    position: absolute; top: 250px; left: 45px; width: 400px;
    display: flex; font-size: 12px;
  }
  .appointment__slot { width: 200px; }
</style>
</head>
<body>
  <section class="card card--front">
    <div class="rule front-line--top"></div>
    <div class="rule front-band"></div>
    <div class="rule front-line--bottom"></div>
    <h1 class="business-name">Bright Crest Detailing</h1>
    <div class="contact">
      <p class="contact__name">Mira Tolland</p>
      <p>Call or text (717) 555-0148</p>
      <p>brightcrestdetails@maildrop-example.com</p>
    </div>
    <div class="socials">
      <p class="socials__item"><span class="socials__mark"></span>@brightcrestdetailing</p>
      <p class="socials__item"><span class="socials__mark"></span>@brightcrestdetailing</p>
    </div>
    <div class="address">
      <p>4175 Quenhollow Rd</p>
      <p>Ashmere PA 17492</p>
    </div>
  </section>

  <section class="card card--back">
    <div class="partners">
      <div class="partner"><span class="partner__circle"></span>Gleamworks</div>
      <div class="partner">Kestrune</div>
    </div>
    <div class="rule back-line--top"></div>
    <div class="rule back-band"></div>
    <div class="rule back-line--bottom"></div>
    <p class="services">Minor paint correction, claying, multi-step buffing and polishing,<br>waxing, hand washes, interior cleaning and more!</p>
    <p class="appointment">
      <svg width="15" height="15" viewBox="0 0 15 15" aria-hidden="true">
        <rect x="1" y="2.5" width="13" height="11.5" fill="none" stroke="#000" stroke-width="1.4"/>
        <rect x="1" y="2.5" width="13" height="3" fill="#000"/>
        <line x1="4.5" y1="0.5" x2="4.5" y2="3.5" stroke="#000" stroke-width="1.4"/>
        <line x1="10.5" y1="0.5" x2="10.5" y2="3.5" stroke="#000" stroke-width="1.4"/>
        <path d="M5.5 8 H9.5 L7 12.5" fill="none" stroke="#000" stroke-width="1.2"/>
      </svg>
      Your next appointment:
    </p>
    <div class="appointment__slots">
      <p class="appointment__slot">Time:</p>
      <p class="appointment__slot">Date:</p>
    </div>
  </section>
</body>
</html>
```